TALMORK

The business want a professional looking business card. We have a scetch we will add but want the extra upgrade, and would like more suggestions for variations of our business cards.

```html
<!DOCTYPE html>
<html lang="en">
<head>
<meta charset="utf-8">
<title>TALMORK – Business Card</title>
<link href="https://fonts.googleapis.com/css2?family=Montserrat:wght@400;500;700&display=swap" rel="stylesheet">
<style>
  :root {
    --stage: #151515;
    --card: #1d1d1d;
    --card-edge: #232323;
    --gold: #d4ae57;
    --gold-light: #ecd28a;
    --gold-dark: #a47d2f;
    --white: #f4f4f4;
    --pattern-dark: #151515;
    --pattern-light: #5a5a5a;
  }
  * { margin: 0; padding: 0; box-sizing: border-box; }
  html, body { width: 1200px; height: 1059px; overflow: hidden; }
  body {
    background: var(--stage);
    font-family: "Montserrat", sans-serif;
    position: relative;
  }
  .card {
    position: absolute;
    width: 690px;
    height: 392px;
    border-radius: 15px;
    background: var(--card);
    overflow: hidden;
  }
  .card--front { left: 257px; top: 89px; }
  .card--back  { left: 255px; top: 546px; }

  .brand {
    position: absolute;
    display: flex;
    flex-direction: column;
    align-items: center;
    gap: 18px;
  }
  .brand__dot {
    width: 44px; height: 44px;
    border-radius: 50%;
    background: var(--gold);
  }
  .brand__name {
    font-family: "Montserrat", sans-serif;
    font-weight: 500;
    font-size: 25px;
    letter-spacing: 7px;
    color: var(--gold);
    line-height: 1;
    padding-left: 7px;
  }
  .card--front .brand { left: 37px; top: 78px; width: 172px; }

  .holder {
    position: absolute;
    right: 38px;
    top: 58px;
    text-align: right;
  }
  .holder__name {
    font-weight: 700;
    font-size: 24px;
    color: var(--gold);
    line-height: 1.1;
  }
  .holder__title {
    font-weight: 400;
    font-size: 19px;
    color: var(--white);
    margin-top: 2px;
  }
  .holder-mark {
    position: absolute;
    right: 0; top: 63px;
    width: 21px; height: 43px;
    background: linear-gradient(180deg, var(--gold-light), var(--gold-dark));
  }

  .contacts {
    position: absolute;
    left: 38px;
    top: 256px;
    list-style: none;
  }
  .contacts__item {
    display: flex;
    align-items: center;
    gap: 10px;
    height: 33.5px;
    font-size: 19px;
    font-weight: 400;
    color: var(--white);
    letter-spacing: 0.2px;
  }
  .contacts__icon { width: 15px; height: 15px; flex: none; }

  .band { position: absolute; bottom: 0; height: 14px; }
  .band--white { left: 0; width: 337px; background: var(--white); }
  .band--gold {
    left: 349px; right: 0;
    background: linear-gradient(180deg, var(--gold-light), var(--gold) 50%, var(--gold-dark));
  }

  .back-pattern {
    position: absolute; inset: 0;
    background:
      radial-gradient(ellipse at 100% 0%, var(--pattern-light) 0%, rgba(90,90,90,0) 65%),
      linear-gradient(135deg, var(--pattern-dark) 0%, #1f1f1f 60%, #2b2b2b 100%);
  }
  .card--back .brand { left: 459px; top: 168px; width: 172px; }
</style>
</head>
<body>

  <section class="card card--front" aria-label="Business card front">
    <div class="brand">
      <span class="brand__dot"></span>
      <span class="brand__name">TALMORK</span>
    </div>

    <div class="holder">
      <p class="holder__name">Anders Holm Vikersund</p>
      <p class="holder__title">CEO &amp; Founder</p>
    </div>
    <span class="holder-mark"></span>

    <ul class="contacts">
      <li class="contacts__item">
        <svg class="contacts__icon" viewBox="0 0 16 16" aria-hidden="true">
          <path fill="var(--gold)" d="M3.6 1.2 6 3.6 4.7 5.4c.8 1.9 2.3 3.4 4.2 4.3l1.7-1.4 2.4 2.4-1.5 2.2C7 12.6 2.9 8.5 1.4 2.7Z"/>
          <path fill="none" stroke="var(--gold)" stroke-width="1.3" d="M9.5 2.2a4.5 4.5 0 0 1 4.3 4.3M9.3 4.7a2 2 0 0 1 2 2"/>
        </svg>
        <span>004791846250</span>
      </li>
      <li class="contacts__item">
        <svg class="contacts__icon" viewBox="0 0 16 16" aria-hidden="true">
          <path fill="var(--gold)" d="M1 6.5 8 2l7 4.5V14H1Z"/>
          <path fill="none" stroke="var(--card)" stroke-width="1.2" d="M1.5 7 8 11l6.5-4M1.5 13.5 6 9.5M14.5 13.5 10 9.5"/>
        </svg>
        <span>talmork.llc@mailbox.com</span>
      </li>
      <li class="contacts__item">
        <svg class="contacts__icon" viewBox="0 0 16 16" aria-hidden="true">
          <circle cx="8" cy="8" r="7" fill="var(--gold)"/>
          <path fill="var(--card)" d="M4 4.5c1.5-.5 3 .3 3.2 1.5.2 1.3-1.2 1.4-1.4 2.6-.2 1.1.8 2 .4 3.3C4.6 11.6 3 10 3 8c0-1.3.4-2.5 1-3.5Zm6 4c1 .2 2 .8 2.3 1.7-.5 1-1.3 1.8-2.3 2.3-.5-1.2-.6-2.7 0-4Z"/>
        </svg>
        <span>www.talmork.llc</span>
      </li>
    </ul>

    <span class="band band--white"></span>
    <span class="band band--gold"></span>
  </section>

  <section class="card card--back" aria-label="Business card back">
    <div class="back-pattern" role="img" aria-label="Repeating tonal pattern fading from black to grey across the card"></div>
    <div class="brand">
      <span class="brand__dot"></span>
      <span class="brand__name">TALMORK</span>
    </div>
  </section>

</body>
</html>
```